Maple Roster Business Card for recruitment company

We are looking for a Business Card Design that incorporates our personal details and our busines name and logo. We are a specialized search consultancy that recruit Property and Construction professionals.
We would like a business card that stands out and is appealing to the Construction and Property industry as well.

Target Market(s)

people in the construction and property industry

Contact Information for Business Card

Business Name and logo

Font styles to use
Serif

Colors
0094D4
00A9DD
6FCCEA
C7EBF8
E9F6FB

Requirements
Must have
• Business name and logo as well as contact details
Should not have
• No photos of us please

```html
<!DOCTYPE html>
<html lang="en">
<head>
<meta charset="utf-8">
<title>Maple Roster Business Card</title>
<link href="https://fonts.googleapis.com/css2?family=Josefin+Sans:wght@300&family=Lato:wght@400;700&display=swap" rel="stylesheet">
<style>
  :root{
    --stage:#d9dadc;
    --navy:#0b3b57;
    --navy-deep:#06283d;
    --navy-glow:#1a5c80;
    --paper:#ffffff;
    --stitch:#8a8286;
    --ink-light:#ffffff;
  }
  *{margin:0;padding:0;box-sizing:border-box}
  html,body{width:1200px;height:800px;overflow:hidden}
  body{background:var(--stage);position:relative;font-family:"Lato",sans-serif}
  .card{position:absolute;left:300px;width:600px;height:343px;border-radius:26px;overflow:hidden;box-shadow:0 6px 18px rgba(0,0,0,.18)}
  .card--front{top:36px;background:var(--navy)}
  .card--back{top:420px;background:var(--navy)}
  .front-shape{position:absolute;inset:0}
  .brand-name{position:absolute;left:38px;top:150px;font-family:"Josefin Sans",sans-serif;font-weight:300;font-size:32px;letter-spacing:2px;color:var(--navy);line-height:1;white-space:nowrap}
  .person{position:absolute;left:100px;top:198px;color:var(--navy);white-space:nowrap}
  .person__name{font-weight:700;font-size:19px;letter-spacing:.5px;line-height:1.1}
  .person__role{font-size:13px;color:#2f4656}
  .contact{position:absolute;right:26px;top:58px;list-style:none;text-align:right;color:var(--ink-light);font-size:13px;line-height:1.32;white-space:nowrap}
  .contact li{display:flex;justify-content:flex-end;align-items:center;gap:8px}
  .contact .gap{margin-top:10px}
  .contact svg{width:13px;height:13px;flex:none}
  .contact .blank{width:13px;flex:none}
  .pattern{position:absolute;inset:0;background:radial-gradient(ellipse at 0% 100%,var(--navy-glow) 0%,var(--navy) 45%,var(--navy-deep) 100%)}
  .back-mark{position:absolute;right:34px;bottom:40px;display:flex;align-items:center;gap:10px;font-family:"Josefin Sans",sans-serif;font-weight:300;font-size:20px;letter-spacing:2px;color:var(--ink-light)}
  .back-mark__dot{width:30px;height:30px;border:2.5px solid var(--ink-light);border-radius:50%}
</style>
</head>
<body>
  <section class="card card--front" aria-label="Business card front">
    <svg class="front-shape" viewBox="0 0 600 343" preserveAspectRatio="none">
      <path d="M0,0 H400 C340,20 360,120 330,190 C300,260 220,285 0,295 Z" fill="var(--paper)"/>
      <path d="M392,0 C332,22 352,122 322,186 C292,254 214,277 0,287" fill="none" stroke="var(--stitch)" stroke-width="1.6" stroke-dasharray="6 4"/>
    </svg>
    <div class="brand-name">MAPLE ROSTER</div>
    <div class="person">
      <div class="person__name">DANIEL HART</div>
      <div class="person__role">President</div>
    </div>
    <ul class="contact">
      <li>214 Cedar Ridge Road <span class="blank"></span></li>
      <li>Calgary, Alberta 20418
        <svg viewBox="0 0 16 16"><path d="M8 1a5 5 0 0 0-5 5c0 4 5 9 5 9s5-5 5-9a5 5 0 0 0-5-5zm0 7a2 2 0 1 1 0-4 2 2 0 0 1 0 4z" fill="#fff"/></svg></li>
      <li class="gap">555-210-4817
        <svg viewBox="0 0 16 16"><path d="M4 1l3 3-2 2c1 2 3 4 5 5l2-2 3 3-2 2C7 14 2 9 2 3z" fill="#fff"/></svg></li>
      <li>555-318-7264
        <svg viewBox="0 0 16 16"><rect x="4" y="1" width="8" height="14" rx="1.5" fill="none" stroke="#fff" stroke-width="1.6"/></svg></li>
      <li>555-402-9135
        <svg viewBox="0 0 16 16"><rect x="2" y="5" width="12" height="9" fill="#fff"/><rect x="5" y="1" width="6" height="4" fill="none" stroke="#fff" stroke-width="1.4"/></svg></li>
      <li>daniel@mapleroster.com
        <svg viewBox="0 0 16 16"><rect x="1" y="3" width="14" height="10" fill="#fff"/><path d="M1 3l7 6 7-6" fill="none" stroke="var(--navy)" stroke-width="1.4"/></svg></li>
      <li>www.mapleroster.com
        <svg viewBox="0 0 16 16"><circle cx="8" cy="8" r="6.5" fill="#fff"/><path d="M1.5 8h13M8 1.5c-3 3-3 10 0 13M8 1.5c3 3 3 10 0 13" fill="none" stroke="var(--navy)" stroke-width="1"/></svg></li>
    </ul>
  </section>

  <section class="card card--back" aria-label="Business card back">
    <div class="pattern" role="img" aria-label="Repeating embossed brand mark pattern across the card back"></div>
    <div class="back-mark"><span class="back-mark__dot"></span>MAPLE ROSTER</div>
  </section>
</body>
</html>
```